VORLAND COMPOSITES INC website in USA

VORLAND COMPOSITES INC incorporated and operated in USA needs a completely new design of website. This Wyoming based company is a importer and distributor of composites material to supply mainly to American and Canadian/Mexican customers. Our main products includes Carbon Fiber, Aramid Fiber, Glass Fiber, Basalt Fiber, High Silica Glass, Quartz Fiber, S-Glass, Alumina Fiber, Vacuum Auxiliary.

We are one stop composites solution provider for Automotive, Aerospace, Construction, Electrical and Machinery industries.

We are exclusive sales company in North America for BLORAN composites produced from China and their other Asia facilities.

Target Market(s)

USA and Canada

Industry/Entity Type

Composites materials

Coding

Coded - Design and coding required

Number of Pages Required

5+ page

Requirements
Nice to have
• Color theme to match our corporate logo VORLAND. VORLAND stands for Northgate Provisioning Trade Holdings

```html
<!DOCTYPE html>
<html lang="en">
<head>
<meta charset="utf-8">
<title>VORLAND Composites Inc.</title>
<link rel="stylesheet" href="https://fonts.googleapis.com/css2?family=Poppins:wght@500;600;700&family=Roboto:wght@400;500;700&display=swap">
<style>
:root{
  --orange:#ee8126;
  --orange-dark:#d96f17;
  --ink:#1e1e1e;
  --black:#0b0b0b;
  --dark:#1c1a19;
  --grey-bg:#f1f1f1;
  --white:#ffffff;
  --muted:#cfcfcf;
}
*{box-sizing:border-box;margin:0;padding:0}
html,body{width:1200px;height:4587px;overflow:hidden}
body{position:relative;background:var(--grey-bg);font-family:"Roboto",Arial,sans-serif;color:var(--ink)}
.abs{position:absolute}
h1,h2,.display{font-family:"Poppins",Arial,sans-serif;font-weight:700}
.accent{color:var(--orange)}
.btn{position:absolute;display:flex;align-items:center;justify-content:center;height:40px;border-radius:20px;font-size:14.5px;font-weight:500;color:var(--white);background:var(--orange)}
.btn-dark{background:#222}
.rule{position:absolute;height:3px;width:100px;background:var(--orange)}
.arrow{position:absolute;width:24px;height:24px}

/* Nav */
.brand{left:143px;top:26px;display:flex;align-items:center;gap:10px}
.brand-mark{width:14px;height:14px;border-radius:50%;background:var(--orange)}
.brand-name{font-family:"Poppins",sans-serif;font-weight:700;font-size:26px;color:var(--orange);letter-spacing:.5px}
.brand-tag{font-family:"Poppins",sans-serif;font-weight:700;font-size:8.5px;line-height:11px;color:var(--orange);width:110px;margin-left:4px}
.nav a{position:absolute;top:36px;font-size:14px;font-weight:500;color:#222;text-decoration:none}
.nav-tab{left:497px;top:0;width:60px;height:94px;background:var(--orange);border-radius:0 0 30px 30px}

/* Hero */
.hero-title{left:0;width:1200px;top:198px;text-align:center;font-size:40px;line-height:46px;color:#1b1b1b}
.hero-sub{left:0;width:1200px;top:308px;text-align:center;font-size:15px;font-weight:500;color:#111}
.dot{position:absolute;left:1118px;width:14px;height:14px;border-radius:50%;background:#bdbdbd}
.scroll-btn{left:575px;top:557px;width:50px;height:50px;border-radius:50%;background:var(--white);display:flex;align-items:center;justify-content:center}

/* About */
.about{left:0;top:660px;width:1200px;height:742px;background:var(--black)}
.about-title{left:601px;top:842px;font-size:38px;color:var(--white)}
.about-copy{left:601px;top:932px;width:452px;font-size:14.5px;line-height:24px;color:#e6e6e6}

/* Products */
.products{left:0;top:1402px;width:1200px;height:601px;background:var(--white)}
.section-title{left:0;width:1200px;text-align:center;font-size:40px;color:#1e1e1e}
.prod{position:absolute;top:1601px;width:290px;height:290px;border-radius:50%;border:4px solid var(--orange);overflow:hidden}
.prod .photo{position:absolute;inset:0}
.prod .band{position:absolute;left:-20px;right:-20px;bottom:0;height:98px;background:var(--orange);border-radius:60% 40% 0 0/40% 30% 0 0;display:flex;justify-content:center;padding-top:24px;font-family:"Poppins",sans-serif;font-weight:700;font-size:19px;color:var(--white)}
.prod.active .band{background:#050505}

/* Partnership */
.partner{left:0;top:2003px;width:1200px;height:720px;background:var(--dark)}
.partner-title{left:142px;top:2088px;font-size:38px;color:var(--white)}
.partner-mark{left:142px;top:2190px;display:flex;align-items:center;gap:10px}
.partner-mark .sq{width:30px;height:30px;background:var(--orange)}
.partner-mark span{font-family:"Poppins",sans-serif;font-weight:700;font-size:28px;color:var(--white);letter-spacing:1px}
.partner-copy{left:144px;top:2272px;width:400px;font-size:14.5px;line-height:24px;color:#eee}

/* Industries */
.ind{position:absolute;top:2800px;height:296px;border-radius:10px;overflow:hidden;border-bottom:5px solid var(--orange)}
.ind.active{border:4px solid var(--orange)}
.ind-label{position:absolute;top:3058px;height:48px;background:var(--white);border-radius:10px 10px 0 0;display:flex;align-items:center;justify-content:center;font-size:16px;font-weight:500;color:#222}
.ind-label.active{top:3064px;background:var(--orange);color:var(--white);border-radius:10px;height:52px;box-shadow:0 4px 10px rgba(0,0,0,.2)}
.ind-caption{left:0;width:1200px;top:3153px;text-align:center;font-size:16px;font-weight:500;color:#222}

/* Contact */
.contact-photo{left:142px;top:3565px;width:428px;height:418px;border-radius:18px;overflow:hidden}
.field{position:absolute;left:600px;width:456px;height:52px;background:var(--white);border-radius:6px;box-shadow:0 2px 8px rgba(0,0,0,.1);font-size:13px;color:#666;padding:18px 16px}

/* Footer */
.footer{left:0;top:3900px;width:1200px;height:687px;background:#121212}
.foot-h{position:absolute;top:4284px;font-size:22px;font-weight:500;color:var(--white)}
.foot-tag{left:144px;top:4330px;font-family:"Poppins",sans-serif;font-weight:600;font-size:18px;line-height:28px;color:var(--orange)}
.foot-copy{left:144px;top:4390px;width:330px;font-size:13.5px;line-height:24px;color:#ddd}
.links{left:604px;top:4330px;list-style:none}
.links li{font-size:13.5px;color:#ddd;height:24px;display:flex;align-items:center;gap:20px}
.links li::before{content:"";width:8px;height:8px;border-radius:50%;background:var(--orange)}
.contact-info{left:842px;top:4330px}
.ci{display:flex;align-items:center;gap:18px;font-size:13.5px;color:#ddd;height:48px}
.ci svg{width:14px;height:14px}
.foot-rule{left:144px;top:4485px;width:912px;height:1px;background:#333}
.social{position:absolute;top:4512px;width:32px;height:32px;border-radius:50%}
.copyright{left:0;width:1200px;top:4520px;text-align:center;font-size:13.5px;color:#ddd}
</style>
</head>
<body>

<!-- Hero -->
<svg class="abs" style="left:0;top:0" width="1200" height="760" viewBox="0 0 1200 760">
  <defs>
    <linearGradient id="heroFill" x1="0" y1="0" x2="0" y2="1">
      <stop offset="0" stop-color="#f4f4f4"/>
      <stop offset=".45" stop-color="#e2e2e2"/>
      <stop offset=".75" stop-color="#9c9c9c"/>
      <stop offset="1" stop-color="#5d5d5d"/>
    </linearGradient>
  </defs>
  <rect x="0" y="640" width="1200" height="120" fill="#0b0b0b"/>
  <path d="M0 398 Q600 1110 1200 398 V0 H0 Z" fill="#ee8126"/>
  <path d="M0 382 Q600 1078 1200 382 V0 H0 Z" fill="url(#heroFill)" role="img" aria-label="Woven carbon fibre fabric photograph"/>
</svg>

<nav class="nav">
  <div class="nav-tab abs"></div>
  <a style="left:510px;color:#fff">Home</a>
  <a style="left:580px">Products</a>
  <a style="left:670px">Industries We Serve</a>
  <a style="left:832px">Partner</a>
  <a style="left:913px">About Us</a>
  <a style="left:1004px">Contact</a>
</nav>
<div class="brand abs">
  <span class="brand-mark"></span>
  <span class="brand-name">VORLAND</span>
  <span class="brand-tag">Northgate Provisioning Trade Holdings</span>
</div>

<h1 class="hero-title abs">Your <span class="accent">One-Stop Source</span> for Advanced<br>Composite <span class="accent">Materials.</span></h1>
<p class="hero-sub abs">Supplying Carbon, Aramid, Glass, and Basalt Fibers across North America.</p>
<a class="btn btn-dark" style="left:419px;top:347px;width:178px">Explore Products</a>
<a class="btn" style="left:604px;top:347px;width:178px">Request a Quote</a>
<span class="dot" style="top:221px;background:var(--orange)"></span>
<span class="dot" style="top:265px"></span>
<span class="dot" style="top:309px"></span>
<div class="scroll-btn abs">
  <svg width="20" height="20" viewBox="0 0 20 20" fill="none" stroke="#111" stroke-width="2.6" stroke-linecap="round" stroke-linejoin="round"><path d="M4 4l6 6 6-6M4 10l6 6 6-6"/></svg>
</div>

<!-- About -->
<section class="about abs"></section>
<div class="abs" role="img" aria-label="Glowing fibre-optic strand bundle" style="left:0;top:748px;width:540px;height:606px;background:radial-gradient(ellipse at 60% 40%,#cfcfcf 0%,#5a5a5a 40%,#0b0b0b 75%)"></div>
<h2 class="about-title abs">About <span class="accent">Us</span></h2>
<span class="rule" style="left:601px;top:906px"></span>
<p class="about-copy abs">Lorem ipsum dolor sit amet, consectetur adipiscing elit, sed do eiusmod tempor incididunt ut labore et dolore magna aliqua. Ut enim ad minim veniam, quis nostrud exercitation ullamco laboris nisi ut aliquip ex ea commodo consequat. Duis aute irure dolor in reprehenderit in voluptate velit esse cillum dolore eu fugiat nulla pariatur. Excepteur sint occaecat cupidatat non proident, sunt in culpa qui officia deserunt mollit anim id est laborum. Lorem ipsum dolor sit amet, consectetur adipiscing elit, sed do eiusmod tempor incididunt ut labore et dolore magna aliqua. Ut enim ad minim veniam, quis nostrud exerci tation ullamco laboris nisi ut aliquip</p>
<a class="btn" style="left:601px;top:1216px;width:146px">Learn More</a>

<!-- Products -->
<section class="products abs"></section>
<h2 class="section-title abs" style="top:1490px"><span class="accent">Our</span> Products</h2>
<span class="rule" style="left:550px;top:1556px"></span>
<svg class="arrow" style="left:61px;top:1743px" viewBox="0 0 24 24" fill="none" stroke="#111" stroke-width="3" stroke-linecap="round" stroke-linejoin="round"><path d="M15 5l-7 7 7 7"/></svg>
<svg class="arrow" style="left:1114px;top:1743px" viewBox="0 0 24 24" fill="none" stroke="#111" stroke-width="3" stroke-linecap="round" stroke-linejoin="round"><path d="M9 5l7 7-7 7"/></svg>
<div class="prod" style="left:140px">
  <div class="photo" role="img" aria-label="Rolls of woven carbon fibre fabric" style="background:linear-gradient(150deg,#6e6e6e,#222 60%,#111)"></div>
  <div class="band">Carbon Fiber</div>
</div>
<div class="prod active" style="left:455px">
  <div class="photo" role="img" aria-label="Loose golden aramid fibre" style="background:radial-gradient(circle at 45% 40%,#f0dfb0,#c9a45c 55%,#8a6a32)"></div>
  <div class="band">Aramid Fiber</div>
</div>
<div class="prod" style="left:769px">
  <div class="photo" role="img" aria-label="Glowing glass fibre strands" style="background:radial-gradient(circle at 60% 40%,#9fe6f0,#2a7fa0 45%,#0d2f4a)"></div>
  <div class="band">Glass Fiber</div>
</div>

<!-- Partnership -->
<section class="partner abs"></section>
<h2 class="partner-title abs">Partnership <span class="accent">With BLORAN</span></h2>
<span class="rule" style="left:142px;top:2156px"></span>
<div class="partner-mark abs"><span class="sq"></span><span>BLORAN</span></div>
<p class="partner-copy abs">VORLAND Composites Inc. is the exclusive sales representative for BLORAN Composites in North America. Through this strategic partnership, we bring Asia's most advanced composite technologies to customers across the U.S., Canada, and Mexico.</p>
<a class="btn" style="left:144px;top:2408px;width:146px">Learn More</a>
<div class="abs" role="img" aria-label="Roll of white woven glass fibre tape" style="left:632px;top:2118px;width:568px;height:342px;border-radius:50% 0 0 50%/60% 0 0 40%;background:radial-gradient(ellipse at 40% 45%,#9a9a95 0%,#e8e6e0 25%,#cfccc5 60%,#8c8a85 100%)"></div>

<!-- Industries -->
<svg class="abs" style="left:0;top:2480px" width="1200" height="960" viewBox="0 2480 1200 960">
  <rect x="0" y="2480" width="1200" height="960" fill="none"/>
  <path d="M0 2676 Q600 2346 1200 2676 V3220 Q600 3550 0 3220 Z" fill="#ee8126"/>
  <path d="M0 2692 Q600 2366 1200 2692 V3204 Q600 3528 0 3204 Z" fill="#ffffff"/>
</svg>
<h2 class="section-title abs" style="top:2680px">Industries <span class="accent">We Serve</span></h2>
<span class="rule" style="left:550px;top:2746px"></span>
<svg class="arrow" style="left:61px;top:2930px" viewBox="0 0 24 24" fill="none" stroke="#111" stroke-width="3" stroke-linecap="round" stroke-linejoin="round"><path d="M15 5l-7 7 7 7"/></svg>
<svg class="arrow" style="left:1114px;top:2930px" viewBox="0 0 24 24" fill="none" stroke="#111" stroke-width="3" stroke-linecap="round" stroke-linejoin="round"><path d="M9 5l7 7-7 7"/></svg>
<div class="ind" style="left:144px;width:214px" role="img" aria-label="Automotive assembly line with robotic arms"><div style="position:absolute;inset:0;background:linear-gradient(160deg,#b9b9b9,#6d5a50 55%,#3a3a3a)"></div></div>
<div class="ind active" style="left:374px;width:220px" role="img" aria-label="Jet engine turbine fan"><div style="position:absolute;inset:0;background:radial-gradient(circle at 50% 40%,#8a8a8a,#3a3a3a 50%,#cfcfcf)"></div></div>
<div class="ind" style="left:609px;width:214px" role="img" aria-label="Building under construction with a crane"><div style="position:absolute;inset:0;background:linear-gradient(180deg,#dcdcdc,#9a9a9a 40%,#2d2d2d)"></div></div>
<div class="ind" style="left:842px;width:214px" role="img" aria-label="Electricity pylons at sunset"><div style="position:absolute;inset:0;background:linear-gradient(180deg,#4f6fb0,#8a86b0 50%,#f1a050 85%,#3a2a20)"></div></div>
<div class="ind-label" style="left:170px;width:162px">Automotive</div>
<div class="ind-label active" style="left:396px;width:170px">Aerospace</div>
<div class="ind-label" style="left:635px;width:162px">Construction</div>
<div class="ind-label" style="left:868px;width:162px">Electrical</div>
<p class="ind-caption abs">Trusted materials powering innovation in the Vorland Composite Inc industry.</p>

<!-- Footer base -->
<section class="footer abs"></section>
<svg class="abs" style="left:0;top:3880px" width="1200" height="340" viewBox="0 3880 1200 340">
  <path d="M0 3880 H1200 V3976 Q600 4440 0 3976 Z" fill="#ee8126"/>
  <path d="M0 3880 H1200 V3960 Q600 4410 0 3960 Z" fill="#f1f1f1"/>
</svg>

<!-- Contact -->
<h2 class="section-title abs" style="top:3465px">Get In <span class="accent">Touch</span></h2>
<div class="contact-photo abs" role="img" aria-label="Stacked rolls of dark basalt fibre mesh" style="background:radial-gradient(circle at 50% 50%,#6a6a6a,#2a2a2a 70%,#151515)"></div>
<div class="field" style="top:3565px">Name</div>
<div class="field" style="top:3638px">Email address</div>
<div class="field" style="top:3711px">Phone</div>
<div class="field" style="top:3783px;height:146px">Message</div>
<a class="btn" style="left:600px;top:3946px;width:146px">Submit Now</a>

<!-- Footer content -->
<h3 class="foot-h" style="left:144px">VORLAND Composites Inc.</h3>
<p class="foot-tag abs">Advanced Materials. Global Reach.<br>Local Expertise.</p>
<p class="foot-copy abs">Lorem ipsum dolor sit amet, consectetur adipiscing elit, sed do eiusmod tempor incididunt ut labore et dolore magna aliqua.</p>
<h3 class="foot-h" style="left:602px">Quick Links</h3>
<ul class="links abs">
  <li>Home</li><li>Products</li><li>Industries</li><li>About</li><li>Contact</li>
</ul>
<h3 class="foot-h" style="left:842px">Contact Info</h3>
<div class="contact-info abs">
  <div class="ci" style="height:24px;margin-bottom:24px"><svg viewBox="0 0 14 14" fill="#ee8126"><path d="M7 0a5 5 0 0 0-5 5c0 3.7 5 9 5 9s5-5.3 5-9a5 5 0 0 0-5-5zm0 7a2 2 0 1 1 0-4 2 2 0 0 1 0 4z"/></svg>Lorem ipsum dolor sit amet,</div>
  <div class="ci" style="height:24px;margin-bottom:24px"><svg viewBox="0 0 14 14" fill="#ee8126"><path d="M3 0l2.5 3.2-1.3 1.8c.9 2 2.5 3.6 4.6 4.6l1.8-1.3L14 10.8 12.6 14C5.7 13.6.4 8.3 0 1.4z"/></svg>+1 888 888 8888</div>
  <div class="ci" style="height:24px"><svg viewBox="0 0 14 14" fill="#ee8126"><path d="M0 2h14v1.2L7 8 0 3.2zM0 4.8L7 9.6l7-4.8V12H0z"/></svg>info@companyname.com</div>
</div>
<div class="foot-rule abs"></div>
<span class="social" style="left:144px;background:var(--orange)"></span>
<span class="social" style="left:184px;background:#333"></span>
<p class="copyright abs">© Copyrights 2025 | All Rights Reserved</p>

</body>
</html>
```